Modern design company business card design

We are a design oriented construction firm. The owner is an architect and licensed General Contractor and accomplished furniture designer. We do new home construction and large scale remodeling and office design. We would like a design for our new business cards that is clean and modern, but relatable. We like the bright green color of our logo mixed with different shades of grey. We're also open to reinterpreting the logo.

Target Market(s)

Potential design clients,
Construction clients

Industry/Entity Type

Architecture

Contact Information for Business Card

Tall Maple Design | Build Inc. (optional with logo, Inc. optional)Jeffrey MorganOwner (optional)317.555.0148 cell317.431.8056 officejmorgan@greensquareinc.comwww.greensquareinc.com

Font styles to use
Sans Serif
Other font styles liked:
• Avenir

Requirements
Nice to have
• I like designs that have some continuity between the front and back, i.e. similar layouts or graphic elements that wrap around the card. I tend to prefer horizontal over vertical, but that's not a have to. I also tend to prefer white or recycled paper.

```html
<!DOCTYPE html>
<html lang="en">
<head>
<meta charset="utf-8">
<title>Tall Maple Design | Build – Business Card</title>
<link rel="stylesheet" href="https://fonts.googleapis.com/css2?family=Mulish:wght@400;600;700&display=swap">
<style>
  :root {
    --backdrop: #4b4b4b;
    --card-white: #ffffff;
    --green: #7cc24e;
    --green-light: #c6df6c;
    --green-deep: #79c45a;
    --grey-text: #555759;
    --grey-name: #8b8e90;
    --grey-rule: #6e7072;
    --grey-band: #9a9c9f;
  }
  * { box-sizing: border-box; margin: 0; padding: 0; }
  html, body {
    width: 1105px; height: 1200px; overflow: hidden;
    background: var(--backdrop);
    font-family: "Mulish", "Avenir", sans-serif;
  }
  .canvas { position: relative; width: 1105px; height: 1200px; }
  .card {
    position: absolute; left: 192px; width: 720px; height: 411px;
    overflow: hidden;
    box-shadow: 0 3px 8px rgba(0,0,0,.45);
  }
  .card--front { top: 146px; background: var(--card-white); }
  .card--back {
    top: 602px;
    background: linear-gradient(180deg, var(--green-light) 0%, var(--green-deep) 100%);
  }

  /* company name, set as plain text in one colour and one weight */
  .company {
    position: absolute;
    font-weight: 600; text-transform: uppercase;
    line-height: 1.15; letter-spacing: 1.5px;
  }
  .company__name { display: block; font-size: 30px; }
  .company__tagline { display: block; font-size: 14px; letter-spacing: 2px; text-align: right; }

  .card--front .company { right: 34px; top: 92px; color: var(--grey-name); text-align: right; }
  .card--back .company { left: 232px; top: 214px; color: var(--card-white); }
  .card--back .company__name { font-size: 34px; }
  .card--back .company__tagline { font-size: 15px; }

  /* person */
  .person { position: absolute; left: 33px; top: 196px; right: 36px; }
  .person__name {
    font-size: 27px; font-weight: 700; color: var(--green);
    text-transform: uppercase; letter-spacing: .3px; line-height: 1;
  }
  .person__role-row { display: flex; align-items: flex-end; gap: 4px; margin-top: 10px; }
  .person__role { font-size: 19px; color: var(--grey-text); text-transform: uppercase; line-height: 1; }
  .person__rule { flex: 1; height: 2px; background: var(--grey-rule); margin-bottom: 2px; }

  /* contact */
  .contact { position: absolute; top: 276px; list-style: none; font-size: 19px; color: var(--grey-text); }
  .contact li { display: flex; align-items: center; gap: 8px; height: 29px; }
  .contact svg { width: 18px; height: 18px; fill: var(--green); flex: none; }
  .contact--phones { left: 35px; }
  .contact--web { right: 30px; }
  .contact--web li { justify-content: flex-end; }

  /* straight footer bands */
  .footer-rule {
    position: absolute; left: 0; right: 0; bottom: 40px; height: 5px;
    background: var(--grey-band);
  }
  .footer-band {
    position: absolute; left: 0; right: 0; bottom: 0; height: 34px;
    background: linear-gradient(90deg, var(--green) 0%, var(--green-light) 60%, var(--green) 100%);
  }
</style>
</head>
<body>
<main class="canvas">

  <section class="card card--front" aria-label="Business card front">
    <p class="company">
      <span class="company__name">Tall Maple</span>
      <span class="company__tagline">Design | Build</span>
    </p>

    <div class="person">
      <h1 class="person__name">Dennis Holloway</h1>
      <div class="person__role-row">
        <span class="person__role">Owner</span>
        <span class="person__rule"></span>
      </div>
    </div>

    <ul class="contact contact--phones">
      <li>
        <svg viewBox="0 0 24 24" aria-hidden="true"><path d="M6.6 10.8a15.1 15.1 0 0 0 6.6 6.6l2.2-2.2c.3-.3.7-.4 1-.2 1.1.4 2.3.6 3.6.6.6 0 1 .4 1 1V20c0 .6-.4 1-1 1A17 17 0 0 1 3 4c0-.6.4-1 1-1h3.5c.6 0 1 .4 1 1 0 1.3.2 2.5.6 3.6.1.3 0 .7-.2 1z"/></svg>
        <span>317.555.0148</span>
      </li>
      <li>
        <svg viewBox="0 0 24 24" aria-hidden="true"><path d="M7 1h10a2 2 0 0 1 2 2v18a2 2 0 0 1-2 2H7a2 2 0 0 1-2-2V3a2 2 0 0 1 2-2zm0 3v14h10V4zm5 15.5a1 1 0 1 0 0 2 1 1 0 0 0 0-2z"/></svg>
        <span>317.555.0172</span>
      </li>
    </ul>

    <ul class="contact contact--web">
      <li>
        <span>www.tallmapleinc.example</span>
        <svg viewBox="0 0 24 24" aria-hidden="true"><circle cx="12" cy="12" r="10"/><path d="M2 12h20M12 2c3 3 3 17 0 20M12 2c-3 3-3 17 0 20" stroke="#fff" stroke-width="1.4" fill="none"/></svg>
      </li>
      <li>
        <span>dholloway@tallmapleinc.example</span>
        <svg viewBox="0 0 24 24" aria-hidden="true"><path d="M2 5h20v14H2z"/><path d="M2 5l10 8 10-8" stroke="#fff" stroke-width="1.6" fill="none"/></svg>
      </li>
    </ul>

    <div class="footer-rule"></div>
    <div class="footer-band"></div>
  </section>

  <section class="card card--back" aria-label="Business card back">
    <p class="company">
      <span class="company__name">Tall Maple</span>
      <span class="company__tagline">Design | Build</span>
    </p>
  </section>

</main>
</body>
</html>
```